Business Card Design for Software Development Company

I am looking for a business card design the incorporates my new logo (attached below).

Key information to include:
Name: Martin Quelbrook
Title: CEO
Email: martin@brightwellcivic.example
Phone: 555-218-9403
Website: www.brightwellcivic.example

NOTE: This design should be easy to edit so that we can order cards for different members of our team.

```html
<!DOCTYPE html>
<html lang="en">
<head>
<meta charset="utf-8">
<title>BrightwellLabs Business Card</title>
<link href="https://fonts.googleapis.com/css2?family=Montserrat:wght@400;500;600;700&display=swap" rel="stylesheet">
<style>
  :root {
    --backdrop: #5c5d60;
    --navy: #31495c;
    --ink: #2b3e50;
    --white: #ffffff;
    --teal: #17a08f;
    --orange: #ee7d2b;
    --red: #c8322b;
  }
  * { margin: 0; padding: 0; box-sizing: border-box; }
  html, body {
    width: 900px; height: 1200px; overflow: hidden;
    background: var(--backdrop);
    font-family: "Montserrat", sans-serif;
  }
  .card {
    position: absolute;
    width: 630px; height: 360px;
    box-shadow: 0 8px 18px rgba(0,0,0,0.35);
  }
  .card-front { left: 135px; top: 213px; background: var(--navy); }
  .card-back { left: 136px; top: 627px; background: var(--white); }

  .wordmark {
    position: absolute;
    display: flex; align-items: center; gap: 10px;
    font-weight: 600; letter-spacing: -0.5px; white-space: nowrap;
  }
  .wordmark-mark { display: block; background: var(--orange); }
  .card-front .wordmark {
    left: 50%; top: 50%; transform: translate(-50%, -50%);
    color: var(--white); font-size: 46px;
  }
  .card-front .wordmark-mark { width: 30px; height: 30px; }
  .card-back .wordmark {
    left: 55px; top: 162px; transform: translateY(-50%);
    color: var(--ink); font-size: 27px; gap: 7px;
  }
  .card-back .wordmark-mark { width: 18px; height: 18px; }

  .divider {
    position: absolute; left: 315px; top: 121px;
    width: 2px; height: 120px; background: var(--ink);
  }
  .contact { position: absolute; left: 333px; top: 120px; color: var(--ink); }
  .contact-name {
    font-size: 23px; font-weight: 700; color: var(--teal);
    line-height: 1.1; letter-spacing: 0.2px;
  }
  .contact-title { font-size: 15px; font-weight: 500; margin-top: 3px; }
  .title-rule {
    width: 30px; height: 2px; margin-top: 3px;
    background: linear-gradient(90deg, var(--teal), var(--orange), var(--red));
  }
  .contact-list { list-style: none; margin-top: 9px; }
  .contact-list li {
    display: flex; align-items: center; gap: 6px;
    font-size: 15px; font-weight: 500; letter-spacing: 0.3px;
    height: 25px;
  }
  .contact-list svg { width: 15px; height: 15px; flex: none; }
</style>
</head>
<body>
  <section class="card card-front">
    <div class="wordmark"><span class="wordmark-mark"></span>BrightwellLabs</div>
  </section>

  <section class="card card-back">
    <div class="wordmark"><span class="wordmark-mark"></span>BrightwellLabs</div>
    <div class="divider"></div>
    <div class="contact">
      <h1 class="contact-name">Martin Quelbrook</h1>
      <p class="contact-title">CEO</p>
      <div class="title-rule"></div>
      <ul class="contact-list">
        <li>
          <svg viewBox="0 0 24 24" aria-hidden="true"><path fill="#d9472b" d="M6.6 10.8a15.1 15.1 0 0 0 6.6 6.6l2.2-2.2c.3-.3.7-.4 1-.2 1.1.4 2.3.6 3.6.6.6 0 1 .4 1 1V20c0 .6-.4 1-1 1A17 17 0 0 1 3 4c0-.6.4-1 1-1h3.5c.6 0 1 .4 1 1 0 1.3.2 2.5.6 3.6.1.3 0 .7-.2 1z"/></svg>
          555-218-9403
        </li>
        <li>
          <svg viewBox="0 0 24 24" aria-hidden="true"><rect x="2" y="5" width="20" height="14" fill="#d9472b"/><path d="M2 5l10 8 10-8" fill="none" stroke="#fff" stroke-width="1.6"/></svg>
          martin@brightwellcivic.example
        </li>
        <li>
          <svg viewBox="0 0 24 24" aria-hidden="true"><circle cx="12" cy="12" r="10" fill="#ee7d2b"/><path d="M2 12h20M12 2c3 3 3 17 0 20M12 2c-3 3-3 17 0 20" fill="none" stroke="#17a08f" stroke-width="1.5"/></svg>
          www.brightwellcivic.example
        </li>
      </ul>
    </div>
  </section>
</body>
</html>
```